Ashmoor Web Design Project

I need the front page and an internal page designed for this client's website. The logo is attached. Obviously the colors have to go with and/or work with the logo colors. I also attached a very rough brochure layout to help you see the direction we're going in with print materials. The rough site map is also attached. I see a slider on the homepage, the art for which I may come back to you to create. This clinic is in a very high end Dallas neighborhood. The hook is that it's a primary care and urgent facility with convenient hours.

I don't know how much this impacts your design, but this will be a Wordpress site and I'm using a framework called Brovila (brovila.com). If Brovila proves to be inflexible, I'll have to get a template that allows me to execute your design.

This site (http://lanternvaleclinic.com) has the type and quality of content I will eventually have on the Ashmoor site.

I just revised the brief for this project. I added the site map and added details to the overview and the "Must Have" section. Thank you for revisiting the brief. 

Reason: Christmas was a bad time to end it.

Target Market(s)

Women 25-54 with children living at home, income over $150k/year

Industry/Entity Type

Clinic

Requirements
Must have
• Masthead incorporating the logo
Followed by the primary nav
Slider on the home page below that
Dual nav - 1 with the nav in the attached site map
2 secondary nav with areas of healthcare
There will three blocks under the nav
1. It's about time (with a small blurb less than 50 words.
2. It's about choices (with small blurb)
3. It's about you (with small blurb)
Three footer blocks
patient check in link on every page
"No appointment? No problem" icon on every page

```html
<!DOCTYPE html>
<html lang="en">
<head>
<meta charset="utf-8">
<title>Ashmoor Medical</title>
<link href="https://fonts.googleapis.com/css2?family=Arimo:wght@400;700&display=swap" rel="stylesheet">
<style>
:root{
  --blue:#0a5a9c;
  --blue-dark:#06467e;
  --blue-link:#0b5aa3;
  --green:#1fb25a;
  --green-light:#2fe07a;
  --green-text:#13a24c;
  --text:#555;
  --white:#fff;
  --line:#ccc;
}
*{box-sizing:border-box;margin:0;padding:0}
html,body{width:1041px;height:1200px;overflow:hidden;background:#fff;font-family:"Arimo",Arial,sans-serif;color:var(--text)}
.page{position:relative;width:1041px;height:1200px;overflow:hidden}
.abs{position:absolute}
.utility{left:754px;top:0;width:184px;height:24px;border:1px solid #ddd;border-top:none;border-radius:0 0 4px 4px;display:flex;gap:14px;justify-content:center;align-items:center;font-size:11px;color:#333;box-shadow:0 1px 2px rgba(0,0,0,.15)}
.social-top{top:34px;display:flex;gap:7px;left:862px}
.social-top span{width:19px;height:19px;background:var(--blue);display:block}
.logo{left:104px;top:46px;display:flex;align-items:center;gap:6px}
.logo .mark{width:38px;height:38px;border-radius:50%;background:var(--blue)}
.logo .name{font-size:25px;font-weight:700;color:var(--blue);line-height:1}
.logo .tag{font-size:8px;color:#444;margin-top:2px;letter-spacing:.2px}
.nav{top:61px;left:394px;display:flex;align-items:center;font-size:12px;color:var(--green-text)}
.nav a{padding:0 14px;line-height:22px;text-decoration:none;color:inherit}
.nav a.active{background:var(--green);color:#fff;padding:0 24px}
.hero{left:104px;top:97px;width:834px;height:301px;border-radius:8px;overflow:hidden}
.hero .photo{position:absolute;left:305px;top:0;width:529px;height:301px;background:linear-gradient(135deg,#6e8f3a,#c46a3a 55%,#9a3a28)}
.hero .side{position:absolute;left:0;top:0;width:305px;height:301px;background:linear-gradient(180deg,#2c78b0,#1b5f98)}
.slide{position:absolute;left:17px;width:280px;height:80px;display:flex;gap:12px;opacity:.55}
.slide.on{opacity:1}
.slide .thumb{width:99px;height:72px;background:#8a8a8a;flex:none}
.slide.on .thumb{background:linear-gradient(135deg,#5f7f3a,#b2683a)}
.slide h4{font-size:10px;color:#fff;font-weight:700;margin-top:2px}
.slide p{font-size:10px;color:#fff;line-height:12px;margin-top:6px}
.slide .more{font-size:9px;color:#fff;font-weight:700;text-align:right;margin-top:4px}
.sep{position:absolute;left:27px;width:261px;height:1px;background:rgba(255,255,255,.6)}
.dropdown{left:521px;top:92px;width:105px;height:115px;background:rgba(255,255,255,.9);border-top:4px solid var(--green);border-radius:0 0 6px 6px;padding:8px 9px;font-size:10px;line-height:14.6px;color:var(--green-text)}
.checkin{left:104px;top:413px;width:834px;height:38px;border-radius:6px;background:linear-gradient(180deg,var(--green-light),var(--green));display:flex;align-items:center;justify-content:center;gap:8px}
.checkin .ico{width:18px;height:18px;border-radius:50%;background:#f2c21b;border:3px solid #3b5e8a}
.checkin .field{width:208px;height:22px;background:#fff;border:1px solid #bbb;font-size:10px;color:#888;padding:5px}
.checkin .btn{width:88px;height:22px;background:linear-gradient(#5fe89a,#23b85d);border:1px solid #fff;color:#fff;font-size:10px;font-weight:700;text-align:center;line-height:20px}
.welcome{left:104px;top:478px;width:566px}
.welcome h1{font-size:15px;font-weight:400;color:var(--blue-link)}
.welcome h1 b{font-weight:400;color:var(--green-text)}
.welcome p{font-size:9.6px;line-height:11.7px;margin-top:12px;padding-left:2px}
.link{font-size:10px;font-weight:700;color:var(--blue-link)}
.promo{left:691px;top:470px;width:247px;height:125px;background:var(--blue);border-radius:6px;color:#fff}
.promo p{position:absolute;left:18px;top:28px;font-size:14px;line-height:18px;text-align:center;width:115px}
.promo .btn{position:absolute;left:29px;top:82px;width:88px;height:23px;background:linear-gradient(#3fcd4a,#1e9a2a);border:1px solid #9be09f;font-size:10px;font-weight:700;text-align:center;line-height:21px}
.promo .clock{position:absolute;left:142px;top:14px;width:92px;height:92px;border-radius:50%;background:radial-gradient(#fff,#bbb)}
.feature{top:622px;width:180px;text-align:center}
.feature .icon{width:92px;height:92px;margin:0 auto;border-radius:50%;background:radial-gradient(circle at 40% 40%,#dfe9f4,#2a6cb4 70%,#123d75)}
.feature h2{font-size:14px;font-weight:400;color:var(--green-text);margin-top:44px}
.feature h2 b{font-weight:400;color:var(--blue-link)}
.feature p{font-size:9.6px;line-height:11.7px;margin-top:12px}
.feature .btn{display:inline-block;margin-top:20px;width:113px;height:29px;border-radius:15px;border:1px solid #bbb;background:linear-gradient(#fff,#e6e6e6);font-size:11px;color:#222;line-height:27px}
.blog{left:691px;top:627px;width:247px}
.blog .head{height:30px;background:var(--green);color:#fff;display:flex;align-items:center;justify-content:space-between;padding:0 8px}
.blog .head h3{font-size:13px}
.blog .head span{font-size:9.5px}
.post{padding:0 8px;margin-top:14px;border-bottom:1px dotted #6b8fb8;padding-bottom:12px}
.post:last-child{border:none}
.post h4{font-size:9.6px;color:var(--blue-link)}
.post h4 i{color:#666;font-weight:400}
.post p{font-size:9.6px;line-height:11.7px;margin-top:12px}
.post p b{color:var(--blue-link);font-weight:400}
.footer{left:104px;top:960px;width:834px;height:260px;background:var(--blue);border-radius:6px 6px 0 0;color:#fff}
.col{position:absolute;top:34px}
.col h5{font-size:12px;margin-bottom:8px}
.col li{list-style:none;font-size:10px;line-height:18px}
.vline{position:absolute;top:34px;width:1px;height:130px;background:rgba(255,255,255,.25)}
.dot{display:inline-block;width:9px;height:9px;background:#fff;margin-right:6px;vertical-align:-1px}
.input{position:absolute;left:573px;width:219px;height:22px;border:1px solid #8fc3ec;background:#0d6fc0;font-size:10px;font-style:italic;font-weight:700;padding:5px 7px}
.send{position:absolute;left:703px;top:168px;width:89px;height:24px;background:linear-gradient(#6ef0a4,#2dc06a);border:1px solid #c6f5d9;text-align:center;line-height:22px;font-size:10px;font-weight:700}
.bottom{position:absolute;top:206px;font-size:10px}
</style>
</head>
<body>
<div class="page">
  <div class="abs utility"><span>Login</span><span>Register</span><span>Blog</span></div>
  <div class="abs social-top"><span></span><span></span><span></span></div>

  <div class="abs logo">
    <div class="mark"></div>
    <div><div class="name">AshmoorMedical</div><div class="tag">Immediate Family and Personal Care</div></div>
  </div>

  <nav class="abs nav">
    <a>HOME</a><a>ABOUT</a><a class="active">SERVICES</a><a>STAFF</a><a>INSURANCE</a><a>VIDEO</a><a>CONTACT US</a>
  </nav>

  <section class="abs hero">
    <div class="photo" role="img" aria-label="Family with two children holding lollipops outdoors"></div>
    <div class="side">
      <div class="slide" style="top:14px"><div class="thumb" role="img" aria-label="Mother with baby"></div><div><h4>LOREM IPSUM DOLOR SIT AMET</h4><p>Lorem ipsum dolor sit amet, conse ctetur adipiscing elit. Cras iaculis n ulla non tellus molestie rhoncus.</p><div class="more">FIND OUT MORE ▸▸</div></div></div>
      <div class="sep" style="top:102px"></div>
      <div class="slide on" style="top:116px"><div class="thumb" role="img" aria-label="Family lying on grass"></div><div><h4>LOREM IPSUM DOLOR SIT AMET</h4><p>Lorem ipsum dolor sit amet, conse ctetur adipiscing elit. Cras iaculis n ulla non tellus molestie rhoncus.</p><div class="more">FIND OUT MORE ▸▸</div></div></div>
      <div class="sep" style="top:203px"></div>
      <div class="slide" style="top:214px"><div class="thumb" role="img" aria-label="Woman at spa treatment"></div><div><h4>LOREM IPSUM DOLOR SIT AMET</h4><p>Lorem ipsum dolor sit amet, conse ctetur adipiscing elit. Cras iaculis n ulla non tellus molestie rhoncus.</p><div class="more">FIND OUT MORE ▸▸</div></div></div>
    </div>
  </section>

  <div class="abs dropdown">Immediate Care<br>Allergies<br>Primary Care<br>Women's Health<br>Medical Spa<br>Men's Health<br>Weight Loss</div>

  <div class="abs checkin"><div class="ico"></div><div class="field">Patient Check In</div><div class="btn">CHECK IN</div></div>

  <section class="abs welcome">
    <h1>Welcome to Ashmoor <b>Medical</b></h1>
    <p>Lorem ipsum dolor sit amet, consectetur adipiscing elit. Cras iaculis nulla non tellus molestie rhoncus. Maecenas blandit aliqu am dolor eget fringilla. Integer egestas dignissim iaculis. Nulla a nibh erat, eu hendrerit erat. Morbi tristique erat et neque lacini a porta. Vestibulum fringilla, felis vel cursus ultrices.</p>
    <p>Magna arcu accumsan nulla, vel euismod lorem est at nibh. Vivamus ac augue ac sapien eleifend tempus. Fusce vel nulla neq ue. Etiam at ante sed ligula aliquam placerat. Curabitur porta pulvinar quam, nec interdum eros fermentum vitae.</p>
    <p class="link" style="margin-top:10px">FIND OUT MORE ▸▸</p>
  </section>

  <aside class="abs promo">
    <p>"No appointment? No problem"</p>
    <div class="btn">LEARN MORE</div>
    <div class="clock" role="img" aria-label="Clock with crossed line and plus sign"></div>
  </aside>

  <div class="abs feature" style="left:97px"><div class="icon" role="img" aria-label="Clock icon"></div><h2>It's <b>about time</b></h2><p>Lorem ipsum dolor sit amet, consectet adipiscing elit. Cras commodo, enim eget ornare convallis, felis orci congue massa, in volutpat magna neque ultrici massa. Vivamus ac mauris elit, non pr risus. Sed cursus, felis nec vehicula auctor, nibh mauris eleifend nisl, a dict um orci turpis sit amet lorem.</p><span class="btn">Keep Reading</span></div>
  <div class="abs feature" style="left:291px"><div class="icon" role="img" aria-label="Arrows choice icon"></div><h2>It's <b>about choices</b></h2><p>Lorem ipsum dolor sit amet, consectet adipiscing elit. Cras commodo, enim eget ornare convallis, felis orci congue massa, in volutpat magna neque ultrici massa. Vivamus ac mauris elit, non pr risus. Sed cursus, felis nec vehicula auctor, nibh mauris eleifend nisl, a dict um orci turpis sit amet lorem.</p><span class="btn">Keep Reading</span></div>
  <div class="abs feature" style="left:492px"><div class="icon" role="img" aria-label="Person icon"></div><h2>It's <b>about you</b></h2><p>Lorem ipsum dolor sit amet, consectet adipiscing elit. Cras commodo, enim eget ornare convallis, felis orci congue massa, in volutpat magna neque ultrici massa. Vivamus ac mauris elit, non pr risus. Sed cursus, felis nec vehicula auctor, nibh mauris eleifend nisl, a dict um orci turpis sit amet lorem.</p><span class="btn">Keep Reading</span></div>

  <section class="abs blog">
    <div class="head"><h3>From Our Blog</h3><span>view blog archieve</span></div>
    <div class="post"><h4>The Title of the post &nbsp;<i>25-12-12</i></h4><p>Lorem ipsum dolor sit amet, consectetur adipiscing elit. Cras commodo, enim eget ornare convallis, felis orci congue massa, in volutpat magna neque ultricies massa. <b>FIND OUT MORE ▸▸</b></p></div>
    <div class="post"><h4>The Title of the post &nbsp;<i>25-12-12</i></h4><p>Lorem ipsum dolor sit amet, consectetur adipiscing elit. Cras commodo, enim eget ornare convallis, felis orci congue massa, in volutpat magna neque ultricies massa. <b>FIND OUT MORE ▸▸</b></p></div>
    <div class="post"><h4>The Title of the post &nbsp;<i>25-12-12</i></h4><p>Lorem ipsum dolor sit amet, consectetur adipiscing elit. Cras commodo, enim eget ornare convallis, felis orci congue massa, in volutpat magna neque ultricies massa. <b>FIND OUT MORE ▸▸</b></p></div>
  </section>

  <footer class="abs footer">
    <div class="col" style="left:41px"><h5>Lorem ipsum dolor</h5><ul><li>Vivamus ac mauris elit</li><li>Morbi a nibh quis</li><li>Phasellus dictum</li><li>Suspendisse libero</li><li>Proin eu ante sed</li><li>Vestibulum sagittis velit</li></ul></div>
    <div class="vline" style="left:180px"></div>
    <div class="col" style="left:217px"><h5>Lorem ipsum dolor</h5><ul><li>Vivamus ac mauris elit</li><li>Morbi a nibh quis</li><li>Phasellus dictum</li><li>Suspendisse libero</li><li>Proin eu ante sed</li><li>Vestibulum sagittis velit</li></ul></div>
    <div class="vline" style="left:361px"></div>
    <div class="col" style="left:401px"><h5>Follow us on</h5><ul><li><span class="dot"></span>Facefolio</li><li><span class="dot"></span>Chirper</li><li><span class="dot"></span>Tubecast</li></ul></div>
    <div class="vline" style="left:514px"></div>
    <div class="col" style="left:576px"><h5>Contact us</h5></div>
    <div class="input" style="top:55px">Name</div>
    <div class="input" style="top:83px">Email</div>
    <div class="input" style="top:111px;height:48px">Your Comments</div>
    <div class="send">SEND</div>
    <div class="bottom" style="left:42px"><span style="opacity:.6">Tel:</span> +1-555-0148392 &nbsp;|&nbsp; <span style="opacity:.6">email:</span> info@ashmoormedical.com</div>
    <div class="bottom" style="left:617px">Copyright © 2012-2013 Ashmoor Medical</div>
  </footer>
</div>
</body>
</html>
```